Brovanek Data Yellow rose letterhead

I have a new logo for my company but in its current form it is too large to be used on letterhead or as a email signature. I need to have the designer use elements from the current logo and create something close to the original but more suited for smaller items.
Updates

I just uploaded a copy of our logo that does not have the weathered affect. Thanks

Reason: More time for revisions

Industry/Entity Type

It Company

Requirements
Must have
• The design must maintain the visual effect of the current logo. It needs to include the yellow rose and the name of the company.
Nice to have
• It would be nice to maintain the stamp theme and incorporate my name, address, phone, email. etc.

```html
<!DOCTYPE html>
<html lang="en">
<head>
<meta charset="utf-8">
<title>Brovanek Data — Letterhead</title>
<link rel="stylesheet" href="https://fonts.googleapis.com/css2?family=Cinzel:wght@700&family=Montserrat:wght@700&display=swap">
<style>
  :root {
    --paper: #ffffff;
    --stamp-gold: #fde7a3;
    --stamp-gold-light: #fff3c8;
    --perf-line: #b9b6b0;
    --panel-centre: #bdb2a0;
    --panel-edge: #b8a274;
    --brand-teal: #82d2da;
    --rose-yellow: #f6cf45;
    --ink: #4b3f3b;
    --rule: #55463f;
  }
  html, body {
    margin: 0;
    padding: 0;
    width: 1194px;
    height: 1200px;
    overflow: hidden;
    background: var(--paper);
  }
  .letterhead {
    display: block;
    width: 1194px;
    height: 1200px;
  }
  .brand-name {
    font-family: "Cinzel", serif;
    font-weight: 700;
    fill: var(--brand-teal);
    letter-spacing: 3px;
  }
  .contact-line {
    font-family: "Montserrat", sans-serif;
    font-weight: 700;
    font-size: 26px;
    fill: var(--ink);
  }
</style>
</head>
<body>
<svg class="letterhead" viewBox="0 0 1194 1200" xmlns="http://www.w3.org/2000/svg">
  <defs>
    <radialGradient id="panel-fill" cx="50%" cy="45%" r="65%">
      <stop offset="0%" stop-color="var(--panel-centre)"/>
      <stop offset="60%" stop-color="#bbad94"/>
      <stop offset="100%" stop-color="var(--panel-edge)"/>
    </radialGradient>
    <linearGradient id="stamp-fill" x1="0" y1="0" x2="1" y2="1">
      <stop offset="0%" stop-color="var(--stamp-gold)"/>
      <stop offset="50%" stop-color="var(--stamp-gold-light)"/>
      <stop offset="100%" stop-color="var(--stamp-gold)"/>
    </linearGradient>
    <clipPath id="stamp-clip">
      <rect x="0" y="0" width="770" height="1197"/>
    </clipPath>
  </defs>

  <!-- stamp body with perforated edge -->
  <g class="stamp" clip-path="url(#stamp-clip)">
    <rect class="stamp-body" x="0" y="0" width="770" height="1197" fill="url(#stamp-fill)"/>
    <g class="perforation" fill="var(--paper)" stroke="var(--perf-line)" stroke-width="2">
      <!-- top -->
      <ellipse cx="46" cy="0" rx="24" ry="27"/>
      <ellipse cx="108" cy="0" rx="24" ry="27"/>
      <ellipse cx="170" cy="0" rx="24" ry="27"/>
      <ellipse cx="232" cy="0" rx="24" ry="27"/>
      <ellipse cx="294" cy="0" rx="24" ry="27"/>
      <ellipse cx="356" cy="0" rx="24" ry="27"/>
      <ellipse cx="418" cy="0" rx="24" ry="27"/>
      <ellipse cx="480" cy="0" rx="24" ry="27"/>
      <ellipse cx="542" cy="0" rx="24" ry="27"/>
      <ellipse cx="604" cy="0" rx="24" ry="27"/>
      <ellipse cx="666" cy="0" rx="24" ry="27"/>
      <ellipse cx="728" cy="0" rx="24" ry="27"/>
      <!-- bottom -->
      <ellipse cx="46" cy="1197" rx="24" ry="27"/>
      <ellipse cx="108" cy="1197" rx="24" ry="27"/>
      <ellipse cx="170" cy="1197" rx="24" ry="27"/>
      <ellipse cx="232" cy="1197" rx="24" ry="27"/>
      <ellipse cx="294" cy="1197" rx="24" ry="27"/>
      <ellipse cx="356" cy="1197" rx="24" ry="27"/>
      <ellipse cx="418" cy="1197" rx="24" ry="27"/>
      <ellipse cx="480" cy="1197" rx="24" ry="27"/>
      <ellipse cx="542" cy="1197" rx="24" ry="27"/>
      <ellipse cx="604" cy="1197" rx="24" ry="27"/>
      <ellipse cx="666" cy="1197" rx="24" ry="27"/>
      <ellipse cx="728" cy="1197" rx="24" ry="27"/>
      <!-- left -->
      <ellipse cx="0" cy="60" rx="27" ry="36"/>
      <ellipse cx="0" cy="178" rx="27" ry="36"/>
      <ellipse cx="0" cy="296" rx="27" ry="36"/>
      <ellipse cx="0" cy="414" rx="27" ry="36"/>
      <ellipse cx="0" cy="532" rx="27" ry="36"/>
      <ellipse cx="0" cy="650" rx="27" ry="36"/>
      <ellipse cx="0" cy="768" rx="27" ry="36"/>
      <ellipse cx="0" cy="886" rx="27" ry="36"/>
      <ellipse cx="0" cy="1004" rx="27" ry="36"/>
      <ellipse cx="0" cy="1122" rx="27" ry="36"/>
      <!-- right -->
      <ellipse cx="770" cy="60" rx="27" ry="36"/>
      <ellipse cx="770" cy="178" rx="27" ry="36"/>
      <ellipse cx="770" cy="296" rx="27" ry="36"/>
      <ellipse cx="770" cy="414" rx="27" ry="36"/>
      <ellipse cx="770" cy="532" rx="27" ry="36"/>
      <ellipse cx="770" cy="650" rx="27" ry="36"/>
      <ellipse cx="770" cy="768" rx="27" ry="36"/>
      <ellipse cx="770" cy="886" rx="27" ry="36"/>
      <ellipse cx="770" cy="1004" rx="27" ry="36"/>
      <ellipse cx="770" cy="1122" rx="27" ry="36"/>
    </g>
  </g>

  <!-- inner panel -->
  <rect class="stamp-panel" x="48" y="63" width="674" height="1073" fill="url(#panel-fill)"/>

  <!-- brand -->
  <g class="brand">
    <circle class="brand-mark" cx="124" cy="142" r="58" fill="var(--rose-yellow)"/>
    <text class="brand-name" x="448" y="104" font-size="44" text-anchor="middle">BROVANEK</text>
    <text class="brand-name" x="448" y="141" font-size="44" text-anchor="middle">DATA</text>
    <line class="brand-rule" x1="203" y1="148" x2="698" y2="148" stroke="var(--rule)" stroke-width="2"/>
  </g>

  <!-- contact block -->
  <g class="contact">
    <line class="contact-rule" x1="61" y1="1006" x2="707" y2="1006" stroke="var(--rule)" stroke-width="2"/>
    <text class="contact-line" x="61" y="1026">Marla Quenton, PhD</text>
    <text class="contact-line" x="61" y="1051">418 NW Cedar Hollow Road, STE 2107</text>
    <text class="contact-line" x="61" y="1076">Pinecrest, TX 75520</text>
    <text class="contact-line" x="61" y="1101">marla@brovanek-data.com</text>
    <text class="contact-line" x="61" y="1126">1-800-555-0147</text>
  </g>
</svg>
</body>
</html>
```